New Business Card for our Indoor Golf Training Facility

We are looking for designs for a new business card for our indoor golf training facility. Attached is our logo, our logo with our slogan, and here is our elevator pitch (What makes us different from the others) not sure if all the info will fit on one card, maybe you can condense the elevator pitch? here is the info

Elevator Pitch
We work with serious golfers and those that want to be serious golfers…
to make you better, faster, at all phases of the game…
We use the same state-of-the-art technology as professional golfers…
which produces data sets that shows your improvement in real time.
Our facility is available 24/7 to our members, which allows you to improve on your time.

our website: www.birchpinlinks.com

Target Market(s)

Golfers

Font styles to use
Serif
Sans Serif

Colors
ec1f27
f59195
fbd4d5
919191
d3d3d3
1b1b1b

Requirements
Must have
• our logo or our logo with the slogan, elevator pitch (can be condensed or shortened)

```html
<!DOCTYPE html>
<html lang="en">
<head>
<meta charset="utf-8">
<title>Birch Pin Links – Business Card</title>
<link rel="stylesheet" href="https://fonts.googleapis.com/css2?family=Open+Sans:wght@400;700&family=Source+Sans+3:ital,wght@0,400;0,700;1,700&display=swap">
<style>
  :root {
    --brand-red: #ec3b33;
    --card-white: #eeeeee;
    --ink: #1b1b1b;
    --rule: #919191;
    --backdrop: #2b2b2b;
    --paper: #ffffff;
  }
  * { margin: 0; padding: 0; box-sizing: border-box; }
  html, body { width: 1200px; height: 1200px; overflow: hidden; }
  body { background: var(--backdrop); position: relative; font-family: "Open Sans", sans-serif; }

  .card { position: absolute; top: 310px; height: 594px; text-align: center; }
  .card--front { left: 234px; width: 364px; background: var(--card-white); color: var(--ink); }
  .card--back { left: 627px; width: 369px; background: var(--brand-red); color: var(--paper); }

  .wordmark { position: absolute; left: 0; right: 0; text-align: center; }
  .wordmark__name { font-family: "Open Sans", sans-serif; font-weight: 700; font-size: 34px; line-height: 1; letter-spacing: -0.3px; }
  .wordmark__slogan { font-family: "Open Sans", sans-serif; font-size: 13px; margin-top: 6px; }
  .card--front .wordmark { top: 160px; color: var(--brand-red); }
  .card--back .wordmark { top: 112px; color: var(--paper); }

  .contact { position: absolute; left: 0; right: 0; top: 356px; font-size: 17px; line-height: 21px; }
  .contact__name { color: var(--brand-red); font-size: 26px; line-height: 30px; }
  .contact__role { font-size: 17px; line-height: 24px; }
  .contact__rule { width: 164px; height: 1px; background: var(--rule); margin: 11px auto 10px; }
  .contact__rule + .contact__address { margin-top: 12px; }

  .pitch { position: absolute; left: 0; right: 0; top: 240px; font-family: "Source Sans 3", sans-serif; font-size: 17.5px; line-height: 21.5px; }
  .pitch__title { font-weight: 700; font-size: 22px; letter-spacing: 0.5px; margin-bottom: 28px; }
  .pitch__para { margin-bottom: 16px; }
  .pitch__rule { width: 304px; height: 1px; background: var(--paper); margin: 20px auto 16px; }
  .pitch__url { font-weight: 700; font-style: italic; }
</style>
</head>
<body>
  <section class="card card--front" aria-label="Business card front">
    <div class="wordmark">
      <div class="wordmark__name">Birch Pin Links</div>
      <div class="wordmark__slogan">Play Well. Train Better. Be Better.</div>
    </div>
    <div class="contact">
      <div class="contact__name">Daniel Hartley</div>
      <div class="contact__role">Managing Director</div>
      <div class="contact__rule"></div>
      <div>555-210-3380</div>
      <div>www.birchpinlinks.com</div>
      <div class="contact__rule"></div>
      <div class="contact__address">1480 Meadowbrook Ave. Unit B3</div>
      <div>Fairview, OH 45099</div>
    </div>
  </section>

  <section class="card card--back" aria-label="Business card back">
    <div class="wordmark">
      <div class="wordmark__name">Birch Pin Links</div>
      <div class="wordmark__slogan">Play Well. Train Better. Be Better.</div>
    </div>
    <div class="pitch">
      <h2 class="pitch__title">ELEVATOR PITCH</h2>
      <p class="pitch__para">We work with serious golfers and those that<br>want to be serious golfers… to make you<br>better, faster, at all phases of the game…</p>
      <p class="pitch__para">We use the same state-of-the-art technology<br>as professional golfers… which produces data<br>sets that shows your improvement in real time.</p>
      <p class="pitch__para">Our facility is available 24/7 to our members<br>which allows you to improve on your time.</p>
      <div class="pitch__rule"></div>
      <p>Visit <span class="pitch__url">www.birchpinlinks.com</span> for more details.</p>
    </div>
  </section>
</body>
</html>
```